TL - business card

Tallow Partners is an insurance brokerage firm, inovative, proactive, vigorous, which aims to become the leader of the insurance brokers in Anfrica. We should like to get some designs which should be avoided also in Gray / Metallic for the Administration and Orange / Blue for the Managers (ike in the picture sent). The Blue / Green logo is not the correct one, but the source of the file. Please adjust the color accordingly for the business cards. 1 / Orange / Blue 2 / Gray / Metallic We want something classic but which is transmitted strenght, inovation, modernity and most of all, rapidity. We want something start-up like, very punchy and catching eye remaining profesional at the same time. Name: Dorian Whitlock Function: Managing Director Address: N ° 17/18 Rua Veloso - R / C 2B Direita - Bairro Mutamba - Luanda Tel: (+244) 947 582 316 Email: dorian.whitlock@tallow-p.example Website: www.tallow-p. example We want classic in the front and creative, colorfull at the back. The cards will be printed in relief, with very high quality of paper.
Insurance Broker
Colors
Designer to choose colors to be used in the design.

```html
<!DOCTYPE html>
<html lang="en">
<head>
<meta charset="utf-8">
<title>Tallow Partners – Business Card</title>
<link rel="stylesheet" href="https://fonts.googleapis.com/css2?family=Michroma&family=Lato:wght@400;700&display=swap">
<style>
  :root {
    --stage: #2b2b2d;
    --brand-blue: #1e9ad6;
    --brand-orange: #f0951c;
    --paper: #f4f4f6;
    --ink: #2a2a2a;
    --rule: #6d6d6d;
  }
  * { margin: 0; padding: 0; box-sizing: border-box; }
  html, body {
    width: 1200px; height: 974px; overflow: hidden;
    background: var(--stage);
  }
  .card {
    position: absolute;
    left: 290px;
    width: 620px; height: 354px;
    box-shadow: 0 18px 40px rgba(0,0,0,0.55);
  }
  .card--back {
    top: 100px;
    background: var(--brand-blue);
    border-right: 6px solid var(--brand-orange);
    border-bottom: 6px solid var(--brand-orange);
  }
  .card--front {
    top: 520px;
    background: var(--paper);
    border-right: 6px solid var(--brand-blue);
    border-bottom: 6px solid var(--brand-blue);
  }
  .brand {
    position: absolute;
    display: flex; flex-direction: column; align-items: center;
  }
  .brand__ring {
    width: 96px; height: 96px;
    border: 7px solid var(--brand-orange);
    border-radius: 50%;
  }
  .brand__name {
    margin-top: 22px;
    font-family: "Michroma", sans-serif;
    font-size: 19px;
    letter-spacing: 0.5px;
    white-space: nowrap;
  }
  .card--back .brand { left: 0; right: 0; top: 96px; }
  .card--back .brand__name { color: #ffffff; }
  .card--front .brand { left: 30px; width: 270px; top: 108px; }
  .card--front .brand__ring { width: 86px; height: 86px; }
  .card--front .brand__name { font-size: 16px; color: var(--brand-orange); }

  .divider {
    position: absolute; left: 316px; top: 80px;
    width: 1.5px; height: 190px; background: var(--rule);
  }
  .contact {
    position: absolute; left: 338px; top: 82px; width: 270px;
    font-family: "Lato", sans-serif; color: var(--ink);
  }
  .contact__name {
    font-family: "Michroma", sans-serif;
    font-size: 16px; line-height: 1.2; white-space: nowrap;
  }
  .contact__first { color: var(--brand-orange); }
  .contact__last { color: var(--brand-blue); }
  .contact__role { font-size: 13.5px; margin-top: 4px; }
  .contact__address { font-size: 13.5px; line-height: 1.35; margin-top: 14px; }
  .contact__list { list-style: none; margin-top: 10px; font-size: 13.5px; }
  .contact__list li { display: flex; align-items: center; gap: 8px; line-height: 1.6; }
  .contact__list svg { width: 12px; height: 12px; flex: none; }
</style>
</head>
<body>
  <section class="card card--back" aria-label="Card back">
    <div class="brand">
      <div class="brand__ring"></div>
      <div class="brand__name">TALLOW PARTNERS</div>
    </div>
  </section>

  <section class="card card--front" aria-label="Card front">
    <div class="brand">
      <div class="brand__ring"></div>
      <div class="brand__name">TALLOW PARTNERS</div>
    </div>
    <div class="divider"></div>
    <div class="contact">
      <p class="contact__name"><span class="contact__first">DORIAN</span> <span class="contact__last">WHITLOCK</span></p>
      <p class="contact__role">Managing Director</p>
      <p class="contact__address">4810 NE Corran Street<br>Halden OR 97410</p>
      <ul class="contact__list">
        <li>
          <svg viewBox="0 0 24 24" aria-hidden="true"><path fill="var(--brand-orange)" d="M6.6 10.8a15.1 15.1 0 0 0 6.6 6.6l2.2-2.2a1 1 0 0 1 1-.25 11.4 11.4 0 0 0 3.6.57 1 1 0 0 1 1 1V20a1 1 0 0 1-1 1A17 17 0 0 1 3 4a1 1 0 0 1 1-1h3.5a1 1 0 0 1 1 1c0 1.25.2 2.45.57 3.57a1 1 0 0 1-.25 1z"/></svg>
          (+244) 947 582 316
        </li>
        <li>
          <svg viewBox="0 0 24 24" aria-hidden="true"><rect x="2" y="5" width="20" height="14" rx="1.5" fill="var(--brand-orange)"/><path d="M3 6l9 7 9-7" stroke="#fff" stroke-width="2" fill="none"/></svg>
          dorian.whitlock@tallow-p.example
        </li>
        <li>
          <svg viewBox="0 0 24 24" aria-hidden="true"><g fill="none" stroke="var(--brand-orange)" stroke-width="2"><circle cx="12" cy="12" r="9.5"/><ellipse cx="12" cy="12" rx="4.5" ry="9.5"/><path d="M2.5 12h19M4 7h16M4 17h16"/></g></svg>
          www.tallow-p. example
        </li>
      </ul>
    </div>
  </section>
</body>
</html>
```